Need Business Card for eLearning Company

Need a business card designed for our company, CareerVantly.

CareerVantly has developed a complete 12 lesson eLearning course to teach you the skills you need to present yourself in a job interview. The course uses advanced learning techniques in the multimedia videos, plus contains quizzes and additional exercises to insure you get the course and can walk into any interview with confidence and ease, and get the job.

www.careervantly-example.com

Industry/Entity Type

Business

```html
<!DOCTYPE html>
<html lang="en">
<head>
<meta charset="utf-8">
<title>CareerVantly Business Card</title>
<link rel="stylesheet" href="https://fonts.googleapis.com/css2?family=Lora:wght@400;700&family=Open+Sans:wght@600&display=swap">
<style>
  :root {
    --bg: #1e1d1c;
    --card-dark: #34302d;
    --card-light: #ffffff;
    --card-light-edge: #ececec;
    --ink: #2f2c2a;
    --ink-soft: #4a4644;
    --on-dark: #f4f2ef;
    --accent: #8a1d6b;
  }
  * { box-sizing: border-box; margin: 0; padding: 0; }
  html, body { width: 1200px; height: 900px; overflow: hidden; }
  body {
    background: var(--bg);
    font-family: "Lora", Georgia, serif;
    display: flex;
    flex-direction: column;
    align-items: center;
    justify-content: center;
    gap: 56px;
  }
  .card {
    width: 620px;
    height: 354px;
    position: relative;
    border-radius: 3px;
    overflow: hidden;
    box-shadow: 0 10px 28px rgba(0,0,0,.45);
  }
  .card--back { background: var(--card-dark); }
  .card--front {
    background: linear-gradient(160deg, var(--card-light) 0%, var(--card-light-edge) 100%);
  }
  .brand {
    position: absolute;
    display: flex;
    align-items: center;
    gap: 16px;
  }
  .brand__square { width: 44px; height: 44px; background: var(--accent); flex: none; }
  .brand__text { display: flex; flex-direction: column; }
  .brand__name {
    font-family: "Lora", Georgia, serif;
    font-weight: 400;
    font-size: 42px;
    line-height: 1;
    letter-spacing: -0.5px;
  }
  .brand__tagline {
    font-family: "Open Sans", Arial, sans-serif;
    font-weight: 600;
    font-size: 11px;
    letter-spacing: 1.4px;
    margin-top: 6px;
  }
  .card--back .brand { left: 160px; top: 142px; color: var(--on-dark); }
  .card--front .brand { left: 60px; top: 34px; color: var(--ink); }
  .person { position: absolute; left: 60px; top: 146px; color: var(--ink); }
  .person__name { font-size: 26px; font-weight: 400; line-height: 1.1; }
  .person__role { font-size: 14px; font-weight: 700; margin-top: 2px; }
  .contacts {
    position: absolute;
    list-style: none;
    color: var(--ink-soft);
    font-size: 15px;
    line-height: 1.5;
  }
  .contacts li { display: flex; align-items: flex-start; gap: 10px; }
  .contacts svg { width: 13px; height: 13px; margin-top: 5px; flex: none; fill: var(--ink); }
  .contacts--personal { left: 60px; top: 206px; }
  .contacts--company { left: 356px; top: 146px; }
  .card__band {
    position: absolute;
    left: 0; right: 0; bottom: 0;
    height: 46px;
    background: var(--card-dark);
  }
</style>
</head>
<body>
  <section class="card card--back" aria-label="Card back">
    <div class="brand">
      <span class="brand__square"></span>
      <div class="brand__text">
        <span class="brand__name">careervantly</span>
        <span class="brand__tagline">INTERVIEW SKILLS ONLINE</span>
      </div>
    </div>
  </section>

  <section class="card card--front" aria-label="Card front">
    <div class="brand">
      <span class="brand__square"></span>
      <div class="brand__text">
        <span class="brand__name">careervantly</span>
        <span class="brand__tagline">INTERVIEW SKILLS ONLINE</span>
      </div>
    </div>

    <div class="person">
      <p class="person__name">Daniel Marlowe</p>
      <p class="person__role">managing director</p>
    </div>

    <ul class="contacts contacts--personal">
      <li>
        <svg viewBox="0 0 16 16" aria-hidden="true"><path d="M3.5 1l2.5 3-1.5 2c.8 2 2.5 3.7 4.5 4.5l2-1.5 3 2.5-1.5 2.5C7 14 2 9 1 2.5z"/></svg>
        212 555 01 47
      </li>
      <li>
        <svg viewBox="0 0 16 16" aria-hidden="true"><path d="M4 0h8a1 1 0 0 1 1 1v14a1 1 0 0 1-1 1H4a1 1 0 0 1-1-1V1a1 1 0 0 1 1-1zm1 2v10h6V2zm3 11a1 1 0 1 0 0 2 1 1 0 0 0 0-2z"/></svg>
        917 555 02 38
      </li>
      <li>
        <svg viewBox="0 0 16 16" aria-hidden="true"><path d="M0 3h16v10H0zm1.5 1.2v.3L8 9l6.5-4.5v-.3z"/></svg>
        dmarlowe@careervantly-example.com
      </li>
    </ul>

    <ul class="contacts contacts--company">
      <li>
        <svg viewBox="0 0 16 16" aria-hidden="true"><path d="M8 0a5.5 5.5 0 0 1 5.5 5.5C13.5 10 8 16 8 16S2.5 10 2.5 5.5A5.5 5.5 0 0 1 8 0zm0 3.3a2.2 2.2 0 1 0 0 4.4 2.2 2.2 0 0 0 0-4.4z"/></svg>
        <span>48 Orchard Lane<br>Brookfield, New York 10472</span>
      </li>
      <li>
        <svg viewBox="0 0 16 16" aria-hidden="true"><path d="M8 0a8 8 0 1 1 0 16A8 8 0 0 1 8 0zm-.7 1.6C5.8 3 5 5.3 4.9 7.3h2.4zm1.4 0v5.7h2.4C11 5.3 10.2 3 8.7 1.6zM1.6 8.7a6.4 6.4 0 0 0 4.3 5.4C4.9 12.6 4.4 10.7 4.3 8.7zm5.7 0H4.9c.1 2 .9 4.3 2.4 5.7zm1.4 0v5.7c1.5-1.4 2.300-3.700 2.4-5.7zm2.8 0c-.1 2-.6 3.9-1.6 5.4a6.4 6.4 0 0 0 4.3-5.4zM1.6 7.3h2.7c.1-2 .6-3.9 1.6-5.4a6.4 6.4 0 0 0-4.3 5.4zm10.1 0h2.7a6.4 6.4 0 0 0-4.3-5.4c1 1.5 1.5 3.4 1.6 5.4z"/></svg>
        www.careervantly-example.com
      </li>
    </ul>

    <div class="card__band"></div>
  </section>
</body>
</html>
```